Fitness Equipment Repair Business Needs a Catchy New Business Card

We have an existing business card, however, it is quite plain and boring. We are expanding primarily in the commercial area (gyms, studios, apartment complexes etc). The business card will serve as eye candy to those managers/owners that can't be met for a face to face.
Originally I was planning for a brochure as well, but all of our information is better summarized on our website. (brightloopservice.ca).
I would like the card to match the colour scheme of the website and utilize the logo. It should have a professional clean feel to it, however, a little colouring outside the lines wouldn't hurt.
The example card is for my service technician (Colin Marsh). If possible I would like to be able to edit the text to use for more than one person.

Industry/Entity Type

Appliance Repair

Contact Information for Business Card

Clean, crisp and professional but needs to be eye catching. Preferably using the black, white and red colour scheme matching the website. Double sided would be nice, but is not necessary.

Colors
ec1f27
ffffff
000000

Requirements
Must have
• Must be able to edit name, phone number and title to use for multiple people. Must show the company website (brightloopservice.ca).

```html
<!DOCTYPE html>
<html lang="en">
<head>
<meta charset="utf-8">
<title>Brightloop Service – Business Card</title>
<link rel="stylesheet" href="https://fonts.googleapis.com/css2?family=Cinzel:wght@400;700&family=PT+Sans:wght@400&display=swap">
<style>
  :root {
    --brand-red: #ec1f27;
    --name-red: #c8141b;
    --ink: #222222;
    --ink-soft: #3a3a3a;
    --panel-black: #050505;
    --panel-glow: #2a2a2a;
    --frost: #ececec;
    --frost-edge: #dcdcdc;
    --logo-grey: #e2e2e2;
    --backdrop: #cdc8c2;
  }
  * { box-sizing: border-box; margin: 0; padding: 0; }
  html, body {
    width: 1200px; height: 969px; overflow: hidden;
    background: var(--backdrop);
  }
  .card {
    position: absolute; left: 100px; top: 200px;
    width: 1000px; height: 568px;
    border-radius: 30px; overflow: hidden;
    display: flex;
    box-shadow: 0 14px 40px rgba(0,0,0,0.18);
  }
  .card__brand {
    position: relative;
    width: 540px; height: 100%;
    background: radial-gradient(ellipse 70% 60% at 45% 30%, var(--panel-glow) 0%, var(--panel-black) 75%);
  }
  .card__divider { width: 4px; height: 100%; background: var(--brand-red); }
  .card__details {
    position: relative; flex: 1; height: 100%;
    background: linear-gradient(135deg, var(--frost) 0%, #f4f4f4 45%, var(--frost-edge) 100%);
    color: var(--ink);
    font-family: "PT Sans", sans-serif;
  }
  .brand-name {
    position: absolute; left: 150px; top: 258px;
    display: flex; align-items: center; gap: 14px;
    font-family: "Cinzel", serif; font-weight: 400;
    font-size: 27px; color: var(--logo-grey); letter-spacing: 0.5px;
  }
  .brand-name__dot {
    width: 14px; height: 14px; border-radius: 50%;
    background: var(--logo-grey);
  }
  .person { position: absolute; left: 50px; top: 104px; }
  .person__name {
    font-family: "Cinzel", serif; font-weight: 700;
    font-size: 35px; color: var(--name-red); line-height: 1;
  }
  .person__title {
    margin-top: 10px;
    font-family: "Cinzel", serif; font-weight: 400;
    font-size: 25px; color: var(--ink-soft); line-height: 1; letter-spacing: 0.5px;
  }
  .address {
    position: absolute; left: 50px; top: 206px;
    font-size: 26px; line-height: 34px; font-style: normal;
  }
  .contacts { position: absolute; left: 50px; top: 298px; list-style: none; }
  .contacts__item {
    display: flex; align-items: center; gap: 12px;
    height: 38px; font-size: 26px;
  }
  .contacts__item small { font-size: 20px; }
  .contacts__icon { width: 24px; height: 24px; flex: none; fill: var(--brand-red); }
</style>
</head>
<body>
  <main class="card">
    <section class="card__brand">
      <div class="brand-name"><span class="brand-name__dot"></span>Brightloop Service</div>
    </section>
    <div class="card__divider"></div>
    <section class="card__details">
      <div class="person">
        <h1 class="person__name">Colin Marsh</h1>
        <p class="person__title">Service technician</p>
      </div>
      <address class="address">1875 Carrow Lane NW<br>Larkfield AB T4X 2K8</address>
      <ul class="contacts">
        <li class="contacts__item">
          <svg class="contacts__icon" viewBox="0 0 24 24"><path d="M6.6 2.5l3 3.2-1.8 2.6c1.2 2.8 3.3 5 6 6.3l2.6-1.8 3.3 3-1.6 3.6C10 19.3 4.5 13.7 3.2 6.1z"/></svg>
          <span>555-410-2386<small>(Personal)</small></span>
        </li>
        <li class="contacts__item">
          <svg class="contacts__icon" viewBox="0 0 24 24"><path d="M6.6 2.5l3 3.2-1.8 2.6c1.2 2.8 3.3 5 6 6.3l2.6-1.8 3.3 3-1.6 3.6C10 19.3 4.5 13.7 3.2 6.1z"/></svg>
          <span>555-730-9142<small>(Service Line)</small></span>
        </li>
        <li class="contacts__item">
          <svg class="contacts__icon" viewBox="0 0 24 24"><rect x="2" y="5" width="20" height="14" rx="1"/><path d="M2.5 5.5L12 13l9.5-7.5" fill="none" stroke="#f2f2f2" stroke-width="1.6"/></svg>
          <span>info@brightloopservice.ca</span>
        </li>
        <li class="contacts__item">
          <svg class="contacts__icon" viewBox="0 0 24 24"><circle cx="12" cy="12" r="10"/><path d="M2 12h20M12 2c3 3 3 17 0 20M12 2c-3 3-3 17 0 20" fill="none" stroke="#f2f2f2" stroke-width="1.3"/></svg>
          <span>brightloopservice.ca</span>
        </li>
      </ul>
    </section>
  </main>
</body>
</html>
```